Health Care Company with Logo Needs Business Cards designed

We are a luxury behavioral health company looking for business cards design we already have a logo and are looking for someone to design a sophisticated luxurious looking business card. Please note that Card design should be captivating just like the logo and also encompass the logo color

Industry/Entity Type

Healthcare

Contact Information for Business Card

Logo,company name, tagline, my name and title, contact details, and physical address

```html
<!DOCTYPE html>
<html lang="en">
<head>
<meta charset="utf-8">
<title>Marlow Behavioral Health – Business Card</title>
<link rel="stylesheet" href="https://fonts.googleapis.com/css2?family=Roboto+Condensed:wght@700&family=Roboto:ital,wght@0,400;0,500;0,700;1,400&display=swap">
<style>
  :root {
    --page-bg: #e9e4dc;
    --card-top: #f7f7f6;
    --card-bottom: #e6e8e9;
    --purple: #74307f;
    --blue: #1a93c8;
    --orange: #f29a1f;
    --ink: #3a3a3a;
    --icon: #7b4a8c;
  }
  * { margin: 0; padding: 0; box-sizing: border-box; }
  html, body {
    width: 1200px; height: 1054px; overflow: hidden;
    background: var(--page-bg);
  }
  .business-card {
    position: absolute; left: 100px; top: 224px;
    width: 1000px; height: 606px;
    border-radius: 22px;
    background: linear-gradient(160deg, var(--card-top), var(--card-bottom));
    box-shadow: 0 18px 40px rgba(60, 50, 40, 0.18);
    overflow: hidden;
    font-family: "Roboto", Arial, sans-serif;
  }
  .brand-mark {
    position: absolute; left: 70px; top: 0; bottom: 0;
    width: 400px;
    display: flex; flex-direction: column; justify-content: center; align-items: flex-start;
    gap: 30px;
  }
  .brand-mark .mark-square {
    width: 110px; height: 110px;
    background: var(--orange);
  }
  .brand-mark .mark-name {
    font-family: "Roboto Condensed", "Arial Narrow", sans-serif;
    font-weight: 700; font-size: 104px; line-height: 1;
    color: var(--purple);
  }
  .info {
    position: absolute; right: 40px; top: 0;
    text-align: right;
  }
  .company-name {
    position: absolute; right: 0; top: 50px; white-space: nowrap;
    font-family: "Roboto Condensed", "Arial Narrow", sans-serif;
    font-weight: 700; font-size: 50px; color: var(--purple);
  }
  .tagline {
    position: absolute; right: 0; top: 118px; white-space: nowrap;
    font-weight: 700; font-size: 16px; letter-spacing: 2.6px;
    color: var(--blue); text-transform: uppercase;
  }
  .person-name {
    position: absolute; right: 0; top: 236px; white-space: nowrap;
    font-weight: 500; font-size: 36px; color: var(--purple);
  }
  .person-title {
    position: absolute; right: 0; top: 286px; white-space: nowrap;
    font-style: italic; font-size: 25px; color: var(--ink);
  }
  .address {
    position: absolute; right: 0; top: 358px; white-space: nowrap;
    font-size: 24px; line-height: 35px; color: var(--ink);
  }
  .contact-list {
    position: absolute; right: 0; top: 444px; list-style: none;
  }
  .contact-list li {
    display: flex; justify-content: flex-end; align-items: center;
    gap: 22px; white-space: nowrap;
    font-size: 24px; line-height: 35px; color: var(--ink);
  }
  .contact-list svg { width: 20px; height: 20px; flex: none; }
</style>
</head>
<body>
  <div class="business-card">
    <div class="brand-mark">
      <div class="mark-square"></div>
      <div class="mark-name">Marlow</div>
    </div>

    <div class="info">
      <div class="company-name">Marlow Behavioral Health</div>
      <div class="tagline">Dedicated to hope, healing and recovery</div>
      <div class="person-name">DANIEL MARLOW</div>
      <div class="person-title">Managing Director</div>
      <div class="address">48 Willow Lane, Cedar Falls,<br>Brookfield, US 204518</div>
      <ul class="contact-list">
        <li>555-204-7781
          <svg viewBox="0 0 20 20" aria-hidden="true"><path fill="var(--icon)" d="M3 8c0-3 3-5 7-5s7 2 7 5h-4V6.5H7V8H3zm2 2h10l2 7H3l2-7zm5 1.5a2.5 2.5 0 1 0 0 5 2.5 2.5 0 0 0 0-5z"/></svg>
        </li>
        <li>daniel@marlowbehavioral.com
          <svg viewBox="0 0 20 20" aria-hidden="true"><rect x="2" y="4" width="16" height="12" fill="var(--icon)"/><path d="M2 4l8 7 8-7" fill="none" stroke="#fff" stroke-width="1.5"/></svg>
        </li>
        <li>www.marlowbehavioral.com
          <svg viewBox="0 0 20 20" aria-hidden="true"><circle cx="10" cy="10" r="8" fill="var(--icon)"/><path d="M2 10h16M10 2c-3 3-3 13 0 16M10 2c3 3 3 13 0 16" fill="none" stroke="#fff" stroke-width="1.2"/></svg>
        </li>
      </ul>
    </div>
  </div>
</body>
</html>
```